Business Card for Industrial Distributor

We need a business card design for an industrial distributor. We sell machine parts for the manufacturing and oil industry. We would like the cards to look clean and modern but with a touch of industry.

Our colors are blue/white.

Please feel free to visit our website www.korvelpartsco.com

Target Market(s)

mexican manufacturers in the automobile/aerospace industry

Industry/Entity Type

Industrial

Colors
ffffff
0555a3

```html
<!DOCTYPE html>
<html lang="en">
<head>
<meta charset="utf-8">
<title>Korvel Business Card</title>
<link rel="stylesheet" href="https://fonts.googleapis.com/css2?family=Arimo:wght@400;700&display=swap">
<style>
  :root {
    --backdrop: #3a322d;
    --card: #151517;
    --brand-blue: #3348c4;
    --brand-blue-light: #4a63e0;
    --text-white: #f2f2f2;
    --text-grey: #9a9aa0;
    --divider: #6a6a70;
  }
  * { margin: 0; padding: 0; box-sizing: border-box; }
  html, body { width: 1200px; height: 864px; overflow: hidden; }
  body {
    background: var(--backdrop);
    font-family: "Arimo", Arial, sans-serif;
    position: relative;
  }
  .card {
    position: absolute;
    width: 560px;
    height: 320px;
    background: var(--card);
    border-radius: 4px;
    box-shadow: 0 10px 30px rgba(0,0,0,.45);
  }
  .card-front { left: 80px; top: 90px; }
  .card-back { left: 560px; top: 454px; }

  .brand-name {
    font-weight: 400;
    color: var(--text-white);
    letter-spacing: 1px;
    white-space: nowrap;
  }
  .front-brand {
    position: absolute;
    left: 0; right: 0; top: 104px;
    text-align: center;
  }
  .front-brand .brand-name { font-size: 44px; }
  .front-url {
    position: absolute; left: 0; right: 0; bottom: 52px;
    text-align: center; color: var(--text-grey);
    font-size: 13px; letter-spacing: 5px;
  }

  .back-brand {
    position: absolute; left: 40px; top: 138px;
    width: 246px;
    text-align: center;
  }
  .back-brand .brand-name { font-size: 32px; }
  .back-divider {
    position: absolute; left: 306px; top: 40px; bottom: 40px;
    width: 1px;
    background: linear-gradient(to bottom, transparent, var(--divider) 20%, var(--divider) 80%, transparent);
  }
  .contact {
    position: absolute; left: 330px; top: 56px; right: 20px;
    color: var(--text-white);
  }
  .contact-name {
    color: var(--brand-blue-light); font-size: 17px; letter-spacing: .5px;
  }
  .contact-title { font-size: 15px; margin-bottom: 12px; }
  .contact-address { font-size: 13px; line-height: 1.35; margin-bottom: 12px; }
  .contact-row {
    display: flex; align-items: center; gap: 9px;
    font-size: 14px; line-height: 1.65;
    white-space: nowrap;
  }
  .contact-row svg { width: 13px; height: 13px; fill: var(--brand-blue-light); flex: none; }
</style>
</head>
<body>
  <section class="card card-front">
    <div class="front-brand">
      <span class="brand-name">Korvel</span>
    </div>
    <p class="front-url">www.korvelpartsco.com</p>
  </section>

  <section class="card card-back">
    <div class="back-brand">
      <span class="brand-name">Korvel</span>
    </div>
    <div class="back-divider"></div>
    <div class="contact">
      <p class="contact-name">MARK ELLISON</p>
      <p class="contact-title">President</p>
      <p class="contact-address">Korvel International Corp.<br>4820 Harbor Line Rd.<br>Eastfield.TX 78590</p>
      <p class="contact-row">
        <svg viewBox="0 0 16 16" aria-hidden="true"><path d="M3 1h3l1.5 4-2 1.2a9 9 0 0 0 4.3 4.3L11 8.5l4 1.5v3a2 2 0 0 1-2 2A13 13 0 0 1 1 3a2 2 0 0 1 2-2z"/></svg>
        (555) 214 - 7730
      </p>
      <p class="contact-row">
        <svg viewBox="0 0 16 16" aria-hidden="true"><path d="M4 1h7v4H4zM1 6h14v7h-3v2H4v-2H1zM5 11v3h6v-3z"/></svg>
        (555) 214 - 7731
      </p>
      <p class="contact-row">
        <svg viewBox="0 0 16 16" aria-hidden="true"><path d="M1 3h14v10H1zM2 4.5v.6l6 4 6-4v-.6z"/></svg>
        sales@korvelpartsco.com
      </p>
      <p class="contact-row">
        <svg viewBox="0 0 16 16" aria-hidden="true"><path d="M8 1a7 7 0 1 0 0 14A7 7 0 0 0 8 1zm0 1.5c.8 1 1.4 2.5 1.6 4.5H6.4C6.6 5 7.2 3.5 8 2.5zM6.4 9h3.2c-.2 2-.8 3.5-1.6 4.5-.8-1-1.4-2.5-1.6-4.5z"/></svg>
        www.korvelpartsco.com
      </p>
    </div>
  </section>
</body>
</html>
```